Business Card Design Project

We need a Business Card for an Mechanical Engineering firm in Singapore. The design should be Modern & Technical looking, yet eye catching.

Our company deals in Cutting Tools & Machine Accessories for the Manufacturing Industries such as Oil & Gas, Aero Space, etc... For more information on our Company, you can either email me or view our website www.torvalen.com.sg.

We are trying to revamp our image to give our consumers a fresh new perspective to our company, so we welcome all ideas.

Industry/Entity Type

Business

Requirements
Must have
• Must incorporate New Company Logo into the card as shown in Uploaded file.

```html
<!DOCTYPE html>
<html lang="en">
<head>
<meta charset="utf-8">
<title>Torvalen Tools – Business Card</title>
<link href="https://fonts.googleapis.com/css2?family=Open+Sans:wght@400;600&display=swap" rel="stylesheet">
<style>
  :root {
    --bg: #d9d9d9;
    --ink-dark: #231f20;
    --brand-red: #8e1b22;
    --paper: #ffffff;
    --text: #2b2b2b;
    --muted-white: #f2f2f2;
  }
  * { box-sizing: border-box; margin: 0; padding: 0; }
  html, body { width: 1200px; height: 951px; overflow: hidden; }
  body {
    background: var(--bg);
    font-family: "Open Sans", Arial, sans-serif;
    position: relative;
  }
  .card {
    position: absolute;
    width: 600px;
    height: 343px;
    border-radius: 22px;
    overflow: hidden;
  }

  /* Back of card */
  .card-back {
    left: 80px; top: 70px;
    background: var(--ink-dark);
  }
  .card-back .edge {
    position: absolute; top: 0; bottom: 0; width: 20px;
    background: var(--brand-red);
  }
  .card-back .edge-left { left: 0; }
  .card-back .edge-right { right: 0; }
  .card-back .brand {
    position: absolute; left: 0; right: 0; top: 120px;
    display: flex; justify-content: center; align-items: center; gap: 14px;
  }
  .brand-dot {
    width: 22px; height: 22px; border-radius: 50%;
    background: var(--brand-red);
  }
  .brand-name {
    font-weight: 600; font-size: 40px; letter-spacing: 1px;
    text-transform: uppercase;
  }
  .card-back .brand-name { color: var(--paper); }
  .card-back .website {
    position: absolute; left: 0; right: 0; top: 232px;
    text-align: center; color: var(--muted-white);
    font-size: 17px; letter-spacing: 0.5px;
  }

  /* Front of card */
  .card-front {
    left: 520px; top: 508px;
    background: var(--paper);
  }
  .card-front .brand {
    position: absolute; left: 44px; top: 58px;
    display: flex; align-items: center; gap: 10px;
  }
  .card-front .brand-dot { width: 16px; height: 16px; }
  .card-front .brand-name { color: var(--brand-red); font-size: 30px; }
  .person {
    position: absolute; right: 44px; top: 76px; text-align: right;
  }
  .person .name {
    font-size: 19px; letter-spacing: 1.5px; color: var(--text);
    text-transform: uppercase;
  }
  .person .role { font-size: 14px; color: var(--brand-red); margin-top: 2px; }
  .contacts {
    position: absolute; left: 44px; top: 168px;
    list-style: none; font-size: 15px; color: var(--text);
  }
  .contacts li { display: flex; align-items: center; gap: 10px; height: 23px; }
  .contacts svg { width: 14px; height: 14px; fill: var(--brand-red); }
  .address {
    position: absolute; right: 44px; top: 214px;
    text-align: right; font-size: 15px; line-height: 22px; color: var(--text);
    font-style: normal;
  }
  .footer-band {
    position: absolute; left: 0; bottom: 0; width: 600px; height: 74px;
  }
  .card-front .website {
    position: absolute; right: 40px; bottom: 12px;
    color: var(--paper); font-size: 16px; letter-spacing: 0.5px;
  }
</style>
</head>
<body>

<section class="card card-back" aria-label="Card back">
  <div class="edge edge-left"></div>
  <div class="edge edge-right"></div>
  <div class="brand">
    <span class="brand-dot"></span>
    <span class="brand-name">Torvalen Tools</span>
  </div>
  <p class="website">www.torvalentools.com</p>
</section>

<section class="card card-front" aria-label="Card front">
  <div class="brand">
    <span class="brand-dot"></span>
    <span class="brand-name">Torvalen Tools</span>
  </div>

  <div class="person">
    <p class="name">Daniel Harrow</p>
    <p class="role">Founder</p>
  </div>

  <ul class="contacts">
    <li>
      <svg viewBox="0 0 16 16" aria-hidden="true"><path d="M3.5 1l2.5 3-1.5 2a8 8 0 0 0 5 5l2-1.5 3 2.5-1.5 2.5C7 15 1 9 1 2.5z"/></svg>
      512-555-0140
    </li>
    <li>
      <svg viewBox="0 0 16 16" aria-hidden="true"><path d="M4 1h8v14H4zM5.5 3v9h5V3z"/></svg>
      512-555-0141
    </li>
    <li>
      <svg viewBox="0 0 16 16" aria-hidden="true"><path d="M1 3h14v10H1zM2.5 4.5 8 9l5.5-4.5z"/></svg>
      info@torvalentools.com
    </li>
  </ul>

  <address class="address">1450 Kestrel Way<br>Dunmore, TX 78110</address>

  <svg class="footer-band" viewBox="0 0 600 74" aria-hidden="true">
    <polygon points="0,20 250,20 272,4 600,4 600,10 275,10 253,26 0,26" fill="var(--brand-red)"/>
    <polygon points="0,32 258,32 280,16 600,16 600,74 0,74" fill="var(--ink-dark)"/>
  </svg>
  <p class="website">www.torvalentools.com</p>
</section>

</body>
</html>
```